TALMEX Stationary and Biz Card design
TALMEX Economic Development Company
TALMEX Stationary and Biz Card design - Financial Services
Creative Brief
Professional
Dennis L Whitaker
CEO
PO BOX 872 HALDEN, OREGON 97311
dena@talmexco.example
talmexco.example
Looking for designs that encompass the strength and integrity of the logo.

```html
<!DOCTYPE html>
<html lang="en">
<head>
<meta charset="utf-8">
<title>TALMEX Business Card</title>
<link href="https://fonts.googleapis.com/css2?family=Open+Sans:wght@400;600;700&display=swap" rel="stylesheet">
<style>
  :root {
    --backdrop: #e9e6e1;
    --card: #ffffff;
    --brand-blue: #1f4e8c;
    --icon-blue: #2a5d9a;
    --ink: #1a1a1a;
    --brand-grey: #6b6e73;
    --watermark: #dde4ef;
    --watermark-edge: #eef2f8;
  }
  * { margin: 0; padding: 0; box-sizing: border-box; }
  html, body {
    width: 1200px;
    height: 778px;
    overflow: hidden;
    background: var(--backdrop);
    font-family: "Open Sans", Arial, sans-serif;
  }
  .business-card {
    position: absolute;
    left: 40px;
    top: 39px;
    width: 1120px;
    height: 700px;
    background: var(--card);
    border-radius: 42px;
    overflow: hidden;
    box-shadow: 0 8px 24px rgba(0,0,0,0.18);
  }
  .crest-backdrop {
    position: absolute;
    left: 560px;
    top: 150px;
    width: 640px;
    height: 640px;
    border-radius: 50%;
    background: radial-gradient(circle at 45% 45%, var(--watermark) 0%, var(--watermark) 45%, var(--watermark-edge) 75%, rgba(255,255,255,0) 100%);
  }
  .brand {
    position: absolute;
    left: 88px;
    top: 170px;
    display: flex;
    align-items: center;
    gap: 22px;
  }
  .brand-dot {
    width: 64px;
    height: 64px;
    border-radius: 50%;
    background: var(--brand-blue);
  }
  .brand-name {
    font-weight: 400;
    font-size: 62px;
    letter-spacing: 10px;
    color: var(--brand-grey);
    line-height: 1;
  }
  .holder {
    position: absolute;
    right: 66px;
    top: 70px;
    text-align: right;
  }
  .holder-name {
    font-weight: 600;
    font-size: 38px;
    color: var(--brand-blue);
    line-height: 1.2;
  }
  .holder-title {
    font-weight: 700;
    font-size: 24px;
    color: var(--ink);
    margin-top: 4px;
  }
  .contact {
    position: absolute;
    left: 58px;
    top: 364px;
    font-size: 27px;
    color: var(--ink);
    line-height: 36px;
    list-style: none;
  }
  .contact li { display: flex; align-items: center; gap: 10px; }
  .contact svg { width: 22px; height: 22px; fill: var(--icon-blue); flex: none; }
</style>
</head>
<body>
  <section class="business-card">
    <div class="crest-backdrop" role="img" aria-label="Large faint brand crest decoration"></div>

    <div class="brand">
      <span class="brand-dot"></span>
      <span class="brand-name">TALMEX</span>
    </div>

    <div class="holder">
      <div class="holder-name">Dennis L Whitaker</div>
      <div class="holder-title">CEO</div>
    </div>

    <ul class="contact">
      <li>PO BOX 872</li>
      <li>Halden, Oregon 97311</li>
      <li>
        <svg viewBox="0 0 24 24" aria-hidden="true"><rect x="7" y="2" width="10" height="20" rx="2"/><rect x="9" y="5" width="6" height="9" fill="#fff"/></svg>
        555 014 2287
      </li>
      <li>
        <svg viewBox="0 0 24 24" aria-hidden="true"><rect x="3" y="9" width="18" height="12" rx="2"/><rect x="6" y="3" width="12" height="7"/><rect x="7" y="13" width="10" height="2" fill="#fff"/></svg>
        555 019 3346
      </li>
      <li>
        <svg viewBox="0 0 24 24" aria-hidden="true"><rect x="2" y="5" width="20" height="14" rx="1"/><path d="M3 6l9 7 9-7" stroke="#fff" stroke-width="2" fill="none"/></svg>
        dena@talmexco.example
      </li>
      <li>
        <svg viewBox="0 0 24 24" aria-hidden="true"><circle cx="12" cy="12" r="10"/><path d="M2 12h20M12 2c3 3 3 17 0 20M12 2c-3 3-3 17 0 20" stroke="#fff" stroke-width="1.6" fill="none"/></svg>
        www.talmexco.example
      </li>
    </ul>
  </section>
</body>
</html>
```